Colin Vardek Business card

Hey there, I’m hoping to have a business card designed. I’m in Real estate and just switched to a new Brokerage called: The Harbourline Property Group

The back could just be the company name maybe or whatever looks good!

I’ve attached some logos of our company and some cards my buddy had done up.

On the card:
Colin Vardek
colinvardek@mailora.com
587-412-9065
colinvardek.ca

Target Market(s)

Home buyers and sellers

Industry/Entity Type

Real Estate

Contact Information for Business Card

just looking for a cool and modern design with my picture on it. I like the idea of Black and red being used.

Requirements
Must have
• all the details provided. I'm open to anything. Just want a professional looking card.

```html
<!DOCTYPE html>
<html lang="en">
<head>
<meta charset="utf-8">
<title>Colin Vardek – Business Card</title>
<link href="https://fonts.googleapis.com/css2?family=Lato:wght@400;700;900&display=swap" rel="stylesheet">
<style>
  :root {
    --bg: #141414;
    --card: #1c1c1d;
    --card-light: #262627;
    --red: #e0203f;
    --white: #f4f4f4;
    --grey: #9a9a9c;
    --silver: #6e6e70;
  }
  * { margin: 0; padding: 0; box-sizing: border-box; }
  html, body { width: 1200px; height: 977px; overflow: hidden; background: var(--bg); font-family: "Lato", sans-serif; }
  .stage { position: relative; width: 1200px; height: 977px; }

  .card {
    position: absolute; left: 250px; width: 700px; height: 400px;
    border-radius: 22px;
    background: radial-gradient(ellipse at 40% 40%, var(--card-light), var(--card) 70%);
    box-shadow: 0 4px 0 var(--red);
    overflow: hidden;
  }
  .card--back { top: 50px; }
  .card--front { top: 512px; }

  /* Back */
  .back-mark {
    position: absolute; left: 0; right: 0; top: 140px;
    display: flex; flex-direction: column; align-items: center; gap: 14px;
  }
  .wordmark { display: flex; align-items: center; gap: 14px; }
  .wordmark__square { width: 18px; height: 18px; background: var(--red); }
  .wordmark__name { font-weight: 900; font-size: 52px; letter-spacing: 1px; color: var(--silver); text-transform: uppercase; }
  .tagline { display: flex; align-items: center; gap: 12px; color: var(--grey); font-size: 13px; letter-spacing: 3px; text-transform: uppercase; }
  .tagline::before, .tagline::after { content: ""; width: 70px; height: 1px; background: var(--grey); }

  /* Front */
  .front-logo { position: absolute; left: 42px; top: 46px; }
  .front-logo .wordmark__name { font-size: 34px; color: var(--white); }
  .front-logo .wordmark__square { width: 13px; height: 13px; }
  .front-logo .tagline { font-size: 9px; letter-spacing: 2px; margin-top: 8px; color: var(--white); }
  .front-logo .tagline::before { width: 24px; }
  .front-logo .tagline::after { width: 24px; }

  .agent { position: absolute; left: 42px; top: 168px; }
  .agent__name { font-weight: 900; font-size: 30px; color: var(--red); text-transform: uppercase; }
  .agent__role { font-size: 17px; color: var(--white); letter-spacing: 1px; margin-top: 2px; }

  .contacts { position: absolute; left: 42px; top: 262px; list-style: none; display: flex; flex-direction: column; gap: 10px; }
  .contacts li { display: flex; align-items: center; gap: 14px; color: var(--white); font-size: 18px; }
  .contacts svg { width: 18px; height: 18px; flex: none; }

  .brokerage {
    position: absolute; right: 40px; top: 40px; width: 270px; text-align: right;
    font-weight: 900; font-size: 24px; line-height: 1.1; color: var(--white); text-transform: uppercase;
  }
  .portrait {
    position: absolute; right: 30px; bottom: 0; width: 260px; height: 280px;
    border-radius: 130px 130px 0 0;
    background: linear-gradient(180deg, #3a3f47 0%, #2a2d33 55%, #1f2024 100%);
  }
  .accent-line { position: absolute; left: 330px; top: 190px; width: 110px; height: 14px; background: linear-gradient(90deg, #5a5a5c, #9a9a9c); }
</style>
</head>
<body>
<main class="stage">

  <section class="card card--back" aria-label="Card back">
    <div class="back-mark">
      <div class="wordmark">
        <span class="wordmark__square"></span>
        <span class="wordmark__name">Colin Vardek</span>
      </div>
      <p class="tagline">The Harbourline Property Group</p>
    </div>
  </section>

  <section class="card card--front" aria-label="Card front">
    <div class="front-logo">
      <div class="wordmark">
        <span class="wordmark__square"></span>
        <span class="wordmark__name">Colin Vardek</span>
      </div>
      <p class="tagline">The Harbourline Property Group</p>
    </div>

    <div class="agent">
      <h1 class="agent__name">Colin Vardek</h1>
      <p class="agent__role">REALTOR</p>
    </div>

    <ul class="contacts">
      <li>
        <svg viewBox="0 0 24 24"><path fill="var(--red)" d="M6.6 10.8a15 15 0 0 0 6.6 6.6l2.2-2.2a1 1 0 0 1 1-.25 11.4 11.4 0 0 0 3.6.57 1 1 0 0 1 1 1V20a1 1 0 0 1-1 1A17 17 0 0 1 3 4a1 1 0 0 1 1-1h3.5a1 1 0 0 1 1 1c0 1.25.2 2.45.57 3.57a1 1 0 0 1-.25 1z"/></svg>
        587-412-9065
      </li>
      <li>
        <svg viewBox="0 0 24 24"><path fill="var(--red)" d="M2 5h20v14H2zm2 2v.5l8 5 8-5V7l-8 5z"/></svg>
        colinvardek@mailora.com
      </li>
      <li>
        <svg viewBox="0 0 24 24"><circle cx="12" cy="12" r="9" fill="none" stroke="var(--red)" stroke-width="2"/><path d="M3 12h18M12 3c3 3 3 15 0 18M12 3c-3 3-3 15 0 18" fill="none" stroke="var(--red)" stroke-width="1.5"/></svg>
        colinvardek.ca
      </li>
    </ul>

    <span class="accent-line"></span>
    <p class="brokerage">The Harbourline Property Group</p>
    <div class="portrait" role="img" aria-label="Portrait photo of the agent in a dark suit and white shirt"></div>
  </section>

</main>
</body>
</html>
```